Flyer für Verkauf von Radondetektoren
Zielgruppe
Ich verkaufe Radondetektoren zur Messung von Radon in Innenräumen. Zielgruppe sind Privatpersonen, Firmen, Genossenschaften und andere Hauseigentümer.
Aufgabenstellung
Ich brauche das Design für meine Messanleitung.
Kreativ - modern - weniger kann mehr sein
Struktur ist wichtigt, es soll also einfach sein zu lesen und zu verstehen, was gemacht werden soll. Können Bulletpoints, Icons mit eingebracht werden.
Wichtig ist auch, dass die beiden Logos 'Luftprüfer.de' und TESTOVAL' auf der Messanleitung vorhanden sind. Wobei 'Luftprüfer.de' das Hauptlogo ist.
DIN format dachte ich A4 beidseitig (Text müsste also auf diese Grösse angepasst werden).
Kann natürlich auch Flyer-Format sein oder andere Vorschläge!
Bildmaterial gibt es auf unsere Homepage https://luftprüfer.de und https://luftkontroll.se . Diese haben wir bereits gekauft und können verwendet werden. Ich lade sie den bei Bedarf hoch. Es können natürlich auch andere Vorschläge kommen.

```html
<!DOCTYPE html>
<html lang="de">
<head>
<meta charset="utf-8">
<title>Messanleitung – Luftprüfer.de</title>
<link href="https://fonts.googleapis.com/css2?family=Barlow:wght@400;600;700&family=Barlow+Semi+Condensed:ital,wght@0,300;0,400;0,700;1,700&display=swap" rel="stylesheet">
<style>
  :root{
    --red:#dc101b;
    --ink:#3b3b3b;
    --text:#2f2f2f;
    --pink-pale:#fbe6e6;
    --pink:#efb3b3;
    --pink-deep:#e17d7f;
    --blue:#1b4f9c;
  }
  *{box-sizing:border-box;margin:0;padding:0}
  html,body{width:1200px;height:848px;overflow:hidden;background:#fff}
  body{font-family:"Barlow Semi Condensed",Arial,sans-serif;color:var(--text);position:relative}
  .abs{position:absolute}

  .step-band{position:absolute;top:28px;height:60px;background:linear-gradient(90deg,#e6e6e6,#cfcfcf)}
  .step-label{position:absolute;top:34px;font-family:"Barlow",Arial,sans-serif;font-size:20px;color:var(--ink);letter-spacing:.5px;font-weight:400}
  .step-label b{font-size:32px;font-weight:700;margin-right:4px}
  .step-badge{position:absolute;top:25px;width:66px;height:66px;border-radius:50%;background:var(--red);border:4px solid #fff;display:flex;align-items:center;justify-content:center}

  h2.section-title{position:absolute;font-family:"Barlow",Arial,sans-serif;font-size:26px;font-weight:700;color:var(--ink);line-height:32px;letter-spacing:.2px}

  .copy{position:absolute;font-size:14px;font-weight:300;line-height:18.6px;text-align:justify}
  .note{position:absolute;font-size:16.5px;font-weight:700;font-style:italic;line-height:21px;color:#111}
  .mode-title{position:absolute;font-family:"Barlow",Arial,sans-serif;font-size:17px;font-weight:700;color:var(--red)}
  .arrow-list{position:absolute;list-style:none;font-size:14px;font-weight:300;line-height:18.6px;text-align:justify}
  .arrow-list li{position:relative}
  .arrow-list li svg{position:absolute;left:-20px;top:4px}

  .return-address{position:absolute;left:468px;top:321px;font-size:14px;line-height:19px;color:var(--red)}
  .return-address b{font-weight:700}

  .hints-title{position:absolute;left:416px;top:483px;font-size:12.8px;font-weight:700;font-style:italic}
  .hints{position:absolute;left:416px;top:500px;width:356px;list-style:none;font-size:12px;font-weight:300;line-height:15px;text-align:justify}
  .hints li{position:relative;padding-left:13px}
  .hints li::before{content:"";position:absolute;left:1px;top:6px;width:4px;height:4px;border-radius:50%;background:var(--red)}
  .legal{position:absolute;left:416px;top:680px;font-size:12px;font-weight:300;line-height:15px}
  .legal strong{font-weight:700;font-style:italic;display:block;font-size:12.8px}

  .partner-mark{position:absolute;left:416px;top:772px;display:flex;align-items:center;gap:8px}
  .partner-mark .dot{width:30px;height:30px;border-radius:50%;background:var(--blue)}
  .partner-mark span{font-family:"Barlow",Arial,sans-serif;font-size:34px;font-weight:600;color:var(--blue);letter-spacing:.5px}

  .cover-top{position:absolute;left:796px;top:0;width:404px;height:28px;background:var(--pink-pale)}
  .cover-head{position:absolute;left:796px;top:28px;width:404px;height:202px;background:var(--red);color:#fff;padding:30px 0 0 32px;font-family:"Barlow",Arial,sans-serif}
  .cover-head h1{font-size:40px;font-weight:700;letter-spacing:1px;line-height:46px}
  .cover-head p{font-size:22px;font-weight:400;line-height:28.5px;margin-top:8px}
  .scene{position:absolute;left:796px;top:230px;width:404px;height:428px;background:linear-gradient(180deg,var(--pink-pale) 0%,var(--pink) 45%,var(--pink-deep) 75%,var(--pink) 100%)}
  .detector-photo{position:absolute;left:826px;top:614px;width:180px;height:104px;border-radius:52px;background:radial-gradient(circle at 40% 35%,#555,#1b1b1b 70%)}

  .brand{position:absolute;right:35px;top:750px;font-family:"Barlow",Arial,sans-serif;font-size:34px;font-weight:400;color:#111;letter-spacing:.3px}
  .tagline{position:absolute;right:35px;top:789px;font-family:"Barlow",Arial,sans-serif;font-size:15px;font-weight:600;color:var(--red);letter-spacing:1.3px}
</style>
</head>
<body>

<div class="step-band" style="left:0;width:330px"></div>
<div class="step-label" style="left:25px"><b>3.</b> SCHRITT</div>
<div class="step-badge" style="left:300px">
  <svg width="36" height="36" viewBox="0 0 36 36" fill="none" stroke="#fff" stroke-width="2.2"><path d="M6 20a12 12 0 1 0 24 0"/><path d="M16 5v15l10-7z" fill="#fff"/></svg>
</div>

<div class="step-band" style="left:392px;width:345px"></div>
<div class="step-label" style="left:417px"><b>4.</b> SCHRITT</div>
<div class="step-badge" style="left:704px">
  <svg width="36" height="36" viewBox="0 0 36 36" fill="#fff"><rect x="5" y="19" width="5" height="9"/><rect x="12" y="12" width="5" height="16"/><rect x="19" y="16" width="5" height="12"/><rect x="26" y="7" width="5" height="21"/><rect x="3" y="30" width="30" height="2.5"/></svg>
</div>

<h2 class="section-title" style="left:25px;top:140px">RADONMESSUNG</h2>
<p class="copy" style="left:44px;top:191px;width:324px;text-align:left">Die Radonmessung beginnt, sobald Sie die radondichten Verpackungen öffnen.</p>

<svg class="abs" style="left:23px;top:246px" width="42" height="42" viewBox="0 0 42 42" fill="none" stroke="var(--red)" stroke-width="4"><rect x="3" y="8" width="29" height="29" rx="5"/><path d="M10 21l8 8L38 4" stroke-linecap="round"/></svg>
<p class="note" style="left:77px;top:248px">Bitte halten Sie die Messdauer<br>wie folgt ein:</p>

<svg class="abs" style="left:23px;top:320px" width="42" height="42" viewBox="0 0 42 42" fill="none" stroke="var(--red)" stroke-width="2.5"><path d="M34 10A18 18 0 1 1 21 3"/><path d="M21 10v11l5 5"/><path d="M31 4l3 6-6 1"/></svg>
<div class="mode-title" style="left:75px;top:335px">Kurzzeitmessung</div>
<ul class="arrow-list" style="left:44px;top:376px;width:324px">
  <li><svg width="14" height="12" viewBox="0 0 14 12" fill="none" stroke="var(--red)" stroke-width="2.2"><path d="M1 1l5 5-5 5M7 1l5 5-5 5"/></svg>Mindestmessdauer 10 Tage (bis hin zu 30 Tagen).</li>
  <li><svg width="14" height="12" viewBox="0 0 14 12" fill="none" stroke="var(--red)" stroke-width="2.2"><path d="M1 1l5 5-5 5M7 1l5 5-5 5"/></svg>Führen Sie die Messung vorzugsweise in der Heizperiode (1. Oktober – 30. April) durch.</li>
  <li><svg width="14" height="12" viewBox="0 0 14 12" fill="none" stroke="var(--red)" stroke-width="2.2"><path d="M1 1l5 5-5 5M7 1l5 5-5 5"/></svg>Kurzzeitmessungen werden oft beim Kauf oder Verkauf von Immobilien genutzt, um ein mögliches Gefährdungspotential abschätzen zu können, oder wenn die Zeit nicht ausreicht, um eine Langzeitmessung durchzuführen.</li>
</ul>

<svg class="abs" style="left:23px;top:543px" width="42" height="42" viewBox="0 0 42 42" fill="none" stroke="var(--red)" stroke-width="2.5"><path d="M8 10A18 18 0 1 0 21 3"/><path d="M21 10v11l5 5"/><path d="M11 4l-3 6 6 1"/></svg>
<div class="mode-title" style="left:75px;top:557px">Langzeitmessung</div>
<ul class="arrow-list" style="left:44px;top:598px;width:324px">
  <li><svg width="14" height="12" viewBox="0 0 14 12" fill="none" stroke="var(--red)" stroke-width="2.2"><path d="M1 1l5 5-5 5M7 1l5 5-5 5"/></svg>Mindestmessdauer 3 Monate während der Heizperiode (1. Oktober – 30. April).</li>
  <li><svg width="14" height="12" viewBox="0 0 14 12" fill="none" stroke="var(--red)" stroke-width="2.2"><path d="M1 1l5 5-5 5M7 1l5 5-5 5"/></svg>Um einen Jahresmittelwert der Radonkonzentration in Innenräumen ermitteln zu können, halten Sie die Messdauer von 12 Monaten ein.</li>
  <li><svg width="14" height="12" viewBox="0 0 14 12" fill="none" stroke="var(--red)" stroke-width="2.2"><path d="M1 1l5 5-5 5M7 1l5 5-5 5"/></svg>Falls Ihr Arbeitsplatz in einem Radon-Vorsorgegebiet liegt und somit der Messpflicht unterliegt, muss die Messdauer von 12 Monaten eingehalten werden.</li>
</ul>

<h2 class="section-title" style="left:416px;top:109px">AUSWERTUNG<br>UND PRÜFBERICHT</h2>
<p class="copy" style="left:416px;top:191px;width:356px">Nach Ablauf der Messdauer, loggen Sie sich wieder auf <b style="font-weight:700">https://kundenportal.testoval.se/de</b> in Ihrem Account ein. Vermerken Sie hier das Ende der Messung und senden Sie anschließend alle Radondetektoren ausreichend frankiert in einem Umschlag oder einem Karton zeitnah an unsere Rücksendeadresse:</p>

<svg class="abs" style="left:416px;top:326px" width="38" height="26" viewBox="0 0 38 26" fill="none" stroke="var(--red)" stroke-width="2.2"><rect x="1.5" y="1.5" width="35" height="23"/><path d="M1.5 1.5L19 15 36.5 1.5M1.5 24.5l13-12M36.5 24.5l-13-12"/></svg>
<div class="return-address"><b>Luftprüfer.de</b><br>Lindenstraße 14, 27568 Musterhafen</div>

<p class="copy" style="left:416px;top:376px;width:356px">Sobald die Radondetektoren im Labor von Testoval eingetroffen sind, werden diese fachgerecht analysiert und die Ergebnisse der Radonmessung ausgewertet. Ein vollständiger Prüfbericht wird Ihnen innerhalb 36 Stunden nach Erhalt der Detektoren im Labor per E-Mail zugeschickt.</p>

<div class="hints-title">Weitere Hinweise</div>
<ul class="hints">
  <li>Bitte beachten Sie, dass die Radonmessung innerhalb von 15 Monaten nach Kaufdatum abgeschlossen sein muss.</li>
  <li>Versuchen Sie nicht das Gehäuse der Detektoren zu öffnen und platzieren Sie diese immer außer Reichweite von Kindern.</li>
  <li>Während der gesamten Messdauer dürfen die Detektoren nicht an einem anderen Ort umplatziert werden.</li>
  <li>Durch die Anmeldung auf der Website https://kundenportal.testoval.se/de und die Eingabe der erforderlichen Daten bestätigt der/die Wohnungseigentümer*in/Messverantwortliche, dass er/sie die Messanleitung befolgt hat und die Detektoren gemäß den Anweisungen korrekt platziert wurden.</li>
</ul>

<div class="legal"><strong>Datenschutz (GDPR), Impressum und AGBs</strong>Mehr Information dazu finden Sie unter www.luftprüfer.de<br>Copyright © 2023 Nordluft Mätteknik AB<br>Alle Rechte vorbehalten www.luftprüfer.de</div>

<div class="partner-mark"><div class="dot"></div><span>Testoval</span></div>

<div class="cover-top"></div>
<div class="cover-head">
  <h1>MESSANLEITUNG</h1>
  <p>für Radonmessungen<br>von Innenraumluft<br>mit passiven Radon Detektoren</p>
</div>
<div class="scene" role="img" aria-label="Illustration einer Stadt mit Hochhäusern, Hügeln, Bäumen und Wohnhäusern in Rottönen"></div>
<div class="detector-photo" role="img" aria-label="Foto von zwei schwarzen passiven Radondetektoren"></div>

<div class="brand">Luftprüfer.de</div>
<div class="tagline">MESSEN STATT VERMUTEN</div>

</body>
</html>
```